Executive Business Card for Healthcare Company [Need Today]

I need a business card design for a healthcare company. The only branding the company has thus far is a logo. The cards will be utilized by company executives. The design I envision will be vibrant and appealing but with a corporate feel. They shouldn't be too casual or playful. I would like to complete this project TODAY if possible.

Target Market(s)

Healthcare vendors, other executives in healthcare and pharmaceuticals

Industry/Entity Type

Pharmaceutical

Contact Information for Business Card

See attachment

Font styles to use
Serif
Sans Serif

Colors

Designer to choose colors to be used in the design.

```html
<!DOCTYPE html>
<html lang="en">
<head>
<meta charset="utf-8">
<title>Corvane Therapeutics – Business Card</title>
<link rel="stylesheet" href="https://fonts.googleapis.com/css2?family=Roboto:wght@300;400&display=swap">
<style>
  :root {
    --backdrop: #3b3b3c;
    --card-dark: #1f1f21;
    --teal: #26b3bd;
    --green: #4bb58a;
    --soft-white: #e6e6e6;
    --muted: #bdbdbd;
    --edge-grey: #8a8a8a;
  }
  * { margin: 0; padding: 0; box-sizing: border-box; }
  html, body {
    width: 799px; height: 1200px; overflow: hidden;
    background: var(--backdrop);
    font-family: "Roboto", Arial, sans-serif;
  }
  .card {
    position: absolute; left: 90px;
    width: 620px; height: 354px;
    background: var(--card-dark);
    box-shadow: 0 18px 40px rgba(0,0,0,.45);
    overflow: hidden;
  }
  .card--front { top: 120px; }
  .card--back { top: 720px; }

  /* Front */
  .front-brand {
    position: absolute; left: 150px; top: 110px;
    display: flex; align-items: center; gap: 18px;
  }
  .brand-circle {
    width: 86px; height: 86px; border-radius: 50%;
    border: 3px solid var(--teal);
  }
  .brand-divider { width: 1px; height: 80px; background: var(--soft-white); }
  .brand-words { line-height: 1; }
  .brand-name {
    font-size: 58px; font-weight: 300; color: var(--teal); letter-spacing: 1px;
  }
  .brand-sub {
    font-size: 27px; font-weight: 300; color: var(--soft-white);
    margin-top: 4px; text-align: right;
  }
  .front-url {
    position: absolute; left: 0; right: 0; top: 272px;
    text-align: center; font-size: 17px; font-weight: 300;
    letter-spacing: 4px; color: var(--soft-white);
  }

  /* Back */
  .back-art { position: absolute; inset: 0; }
  .person { position: absolute; left: 46px; top: 38px; }
  .person-name { font-size: 24px; font-weight: 400; color: var(--teal); }
  .person-title { font-size: 11px; font-weight: 300; color: var(--soft-white); margin-top: 4px; }
  .contact {
    position: absolute; left: 46px; top: 190px;
    list-style: none; color: var(--soft-white);
    font-size: 15px; font-weight: 300; line-height: 21px;
  }
  .contact li { display: flex; align-items: center; gap: 8px; }
  .contact svg { width: 12px; height: 12px; fill: var(--teal); flex: none; }
  .contact .no-icon { padding-left: 0; }
  .back-brand {
    position: absolute; left: 460px; top: 290px;
    transform: rotate(-90deg); transform-origin: left top;
    display: flex; align-items: center; gap: 14px;
  }
  .back-brand .brand-circle { width: 70px; height: 70px; border-color: #fff; }
  .back-brand .brand-divider { height: 62px; background: #fff; }
  .back-brand .brand-name { font-size: 46px; color: #fff; }
  .back-brand .brand-sub { font-size: 21px; color: #fff; }
</style>
</head>
<body>
  <section class="card card--front">
    <div class="front-brand">
      <div class="brand-circle"></div>
      <div class="brand-divider"></div>
      <div class="brand-words">
        <div class="brand-name">corvane</div>
        <div class="brand-sub">therapeutics</div>
      </div>
    </div>
    <p class="front-url">www.corvanerx.com</p>
  </section>

  <section class="card card--back">
    <svg class="back-art" viewBox="0 0 620 354" width="620" height="354">
      <defs>
        <linearGradient id="panelFill" x1="0" y1="0" x2="1" y2="1">
          <stop offset="0" stop-color="#1fb1c6"/>
          <stop offset="1" stop-color="#4db686"/>
        </linearGradient>
      </defs>
      <path d="M480 0 C440 40 440 110 420 170 C400 240 372 290 362 354 L352 354 C362 290 390 240 410 170 C430 110 430 40 470 0 Z" fill="var(--edge-grey)"/>
      <path d="M480 0 C440 40 440 110 420 170 C400 240 372 290 362 354 L620 354 L620 0 Z" fill="url(#panelFill)"/>
    </svg>

    <div class="person">
      <h1 class="person-name">Martin Ellwood</h1>
      <p class="person-title">Senior Director of Marketing</p>
    </div>

    <ul class="contact">
      <li><svg viewBox="0 0 12 12"><path d="M2 1h3l1 3-1.5 1a6 6 0 0 0 2.5 2.5L8 6l3 1v3a1 1 0 0 1-1 1A9 9 0 0 1 1 2a1 1 0 0 1 1-1z"/></svg>555-014-2280</li>
      <li><svg viewBox="0 0 12 12"><path d="M3 0h6a1 1 0 0 1 1 1v10a1 1 0 0 1-1 1H3a1 1 0 0 1-1-1V1a1 1 0 0 1 1-1zm0 2v7h6V2z"/></svg>555-017-6614</li>
      <li><svg viewBox="0 0 12 12"><path d="M6 0a6 6 0 1 0 0 12A6 6 0 0 0 6 0zm0 1.5c.8 1 1.2 2.6 1.3 3.8H4.7C4.8 4.1 5.2 2.5 6 1.5zM4.7 6.7h2.6c-.1 1.2-.5 2.8-1.3 3.8-.8-1-1.2-2.6-1.3-3.8z"/></svg>mellwood@corvanerx.com</li>
      <li>118 W Laurel Avenue</li>
      <li>Dalton, GA 30720</li>
    </ul>

    <div class="back-brand">
      <div class="brand-circle"></div>
      <div class="brand-divider"></div>
      <div class="brand-words">
        <div class="brand-name">corvane</div>
        <div class="brand-sub">therapeutics</div>
      </div>
    </div>
  </section>
</body>
</html>
```